Quintel Packaging Business Card

Project Overview
We are seeking a modern, minimalist business card that effectively represents our company while making a bold and lasting impression. The design should reflect trust, professionalism, and innovation, reinforcing our expertise in custom plastic manufacturing for warehouse and distribution centers.

Provided Assets & Specifications
Logo: We will provide our official logo for integration into the design.
Design Files: Photoshop (PSD) files for our printing specifications will be supplied.

Card Size & Material:
Dimensions: 3.5" x 2"
Material: 1/8" Radius Plastic Business Cards with 1/8" Rounded Corners
Clear plastic background—the design should strategically incorporate transparency.
Orientation: The card should be designed in landscape format for a sleek and professional presentation.

Design Requirements:
Logo Prominence
The logo must be the focal point of the card.
Space should be used effectively to draw attention to the logo while maintaining a minimalist layout.

Clear Plastic Integration
The transparent background should create the illusion of blank space, enhancing the modern and high-quality feel.
Avoid any frosted effects—we do not want white areas to appear semi-transparent.

Minimalist & Impactful
Clean, structured, and easy to read at a glance.
Focus on sharp contrast to ensure legibility and visibility.
The design should instill confidence and reflect our role as a leading plastics manufacturer.

Color Palette & Contrast
Primary Colors: Blue, Black, White, and Grey
Use bold black or blue for text and key elements to ensure they stand out against the clear plastic.
Avoid light, pastel, or neon colors that may fade into the plastic background.
No frosted or semi-transparent white—we do not want a cloudy effect.

Typography & Information Hierarchy
Bold, modern typography—clear, professional, and highly legible.
The business card should highlight:
Company Logo (Primary Focus)
Full Name & Title
Phone Number
Email
Website

Brand Representation
The card should reflect our expertise in manufacturing high-quality custom plastics for large-scale packaging and distribution businesses.
Our clients rely on us to enhance their brand presence through custom plastic solutions, and our business cards should reinforce that sense of precision and trust.

Final Considerations
Utilize the clear plastic effectively to differentiate our brand from standard business cards.
Maintain a sleek, professional aesthetic while ensuring all text and elements remain legible.
The design should align with our industry, conveying reliability and innovation.
We look forward to seeing a design that captures our brand identity, maximizes the clear plastic medium, and makes a strong, professional impact on our clients.

```html
<!DOCTYPE html>
<html lang="en">
<head>
<meta charset="utf-8">
<title>Quintel Packaging Business Card</title>
<link rel="stylesheet" href="https://fonts.googleapis.com/css2?family=Lato:wght@400;700&display=swap">
<style>
  :root {
    --page-bg: #dfe5ec;
    --card-clear: #f5f7f9;
    --card-edge: #c9d1da;
    --ink-dark: #3a3b3d;
    --ink-text: #2f3033;
    --brand-blue: #1d6aa3;
    --icon-blue: #2a6f95;
  }
  * { margin: 0; padding: 0; box-sizing: border-box; }
  html, body {
    width: 1200px;
    height: 900px;
    overflow: hidden;
    background: var(--page-bg);
    font-family: "Lato", Arial, sans-serif;
  }
  .card {
    position: absolute;
    left: 75px;
    top: 150px;
    width: 1050px;
    height: 600px;
    background: var(--card-clear);
    border: 1px solid var(--card-edge);
    border-radius: 38px;
    overflow: hidden;
  }
  .company-name {
    position: absolute;
    left: 56px;
    top: 74px;
    font-size: 46px;
    font-weight: 700;
    color: var(--ink-dark);
    letter-spacing: 0.5px;
    white-space: nowrap;
  }
  .brand-square {
    position: absolute;
    left: 610px;
    top: 120px;
    width: 360px;
    height: 360px;
    background: var(--brand-blue);
  }
  .person-name {
    position: absolute;
    left: 58px;
    top: 236px;
    font-size: 36px;
    font-weight: 700;
    color: var(--ink-dark);
    letter-spacing: 0.3px;
  }
  .person-title {
    position: absolute;
    left: 58px;
    top: 284px;
    font-size: 26px;
    font-weight: 400;
    color: var(--ink-text);
  }
  .contact-list {
    position: absolute;
    left: 58px;
    top: 352px;
    list-style: none;
  }
  .contact-item {
    display: flex;
    align-items: center;
    height: 46px;
    font-size: 26px;
    color: var(--ink-text);
  }
  .contact-icon {
    width: 26px;
    height: 26px;
    margin-right: 26px;
    flex: none;
  }
  .address {
    position: absolute;
    left: 58px;
    top: 496px;
    font-size: 26px;
    line-height: 42px;
    color: var(--ink-text);
    font-style: normal;
  }
</style>
</head>
<body>
  <div class="card">
    <div class="company-name">Quintel Packaging</div>
    <div class="brand-square"></div>

    <div class="person-name">MARCUS HALE</div>
    <div class="person-title">Owner</div>

    <ul class="contact-list">
      <li class="contact-item">
        <svg class="contact-icon" viewBox="0 0 24 24" aria-hidden="true">
          <path fill="var(--icon-blue)" d="M6.6 10.8c1.4 2.8 3.8 5.1 6.6 6.6l2.2-2.2c.3-.3.7-.4 1-.2 1.1.4 2.3.6 3.6.6.6 0 1 .4 1 1V20c0 .6-.4 1-1 1C10.6 21 3 13.4 3 4c0-.6.4-1 1-1h3.5c.6 0 1 .4 1 1 0 1.3.2 2.5.6 3.6.1.3 0 .7-.2 1z"/>
        </svg>
        044-555 010 203
      </li>
      <li class="contact-item">
        <svg class="contact-icon" viewBox="0 0 24 24" aria-hidden="true">
          <rect x="2" y="5" width="20" height="14" rx="1.5" fill="var(--icon-blue)"/>
          <path d="M3 6.5l9 6.5 9-6.5" fill="none" stroke="var(--card-clear)" stroke-width="1.8"/>
        </svg>
        hello@quintelpack.com
      </li>
      <li class="contact-item">
        <svg class="contact-icon" viewBox="0 0 24 24" aria-hidden="true">
          <circle cx="12" cy="12" r="9.5" fill="none" stroke="var(--icon-blue)" stroke-width="2"/>
          <ellipse cx="12" cy="12" rx="4" ry="9.5" fill="none" stroke="var(--icon-blue)" stroke-width="1.8"/>
          <path d="M2.5 12h19M4 7.5h16M4 16.5h16" stroke="var(--icon-blue)" stroke-width="1.6"/>
        </svg>
        www.quintelpack.com
      </li>
    </ul>

    <address class="address">421, Address line goes<br>here, 52, Country name</address>
  </div>
</body>
</html>
```